Etikett für Rotweinflasche
Liebe farbkosmos Atelier, wir werden uns bei der endgültigen Etikettengestaltung (finale Größe + Rückseite) noch an Euch melden. Bitte sendet uns euren Kontakt an helga.brandt@morvelli.wine
Zielgruppe
Morvelli Italia ist ein exklusives Boutique-Weingut in Sizilien, das hochqualitative Spitzenweine in kleinen Mengen mit modernster Technologie und stets nachhaltig erzeugt. Wir hinterfragen sowohl in der Agronomie im Weingarten als auch in der Önologie im Weinkeller alle herrschenden Traditionen und trachten danach, stets das beste Endprodukt zu kreieren. Der vulkanische, kalkreiche Boden Siziliens sowie trockene, sonnenreiche und niederschlagsarme Vegetationsperioden sind unsere optimale Basis.
Zielgruppe: Internationale Genussmenschen jeglichen Alters, die sich bewusst auch höherpreisige Weine (um die €30+) gönnen , vor allem kunstaffine young professionals mit Qualitäts-& Nachhaltigkeitsanspruch
Aufgabenstellung
Das Etikett ist für Rotwein-Flaschen (Cabernet Sauvignon / Nero D'Avola / Frappato / Syrah / Cerasuolo / Petit Verdot / sowie einen Bourdeaux-Cuveè aus Cabernet Sauvignon und Petit Verdot) .
Die Flasche ist reinschwarz, sehr hochwertig und schwer.
Flaschenform: Bordeauxflasche siehe technisches Datenblatt
Sleeve über dem Korken: schwarz mit weißer Schrift wie bisher
Zu gestalten ist das Etikett der Vorderseite. Zumindest die jeweilige Rotwein-Sorte ist auch textlich darzustellen (zwecks Scannen mit Trubel-App)
Der Kreativität kann freien Lauf gelassen werden! Unterscheidbarkeit vom Markt ist explizit gewollt.
Unsere aktuellen Etiketten und Markenauftritt siehe: https://morvelli.wine/shop/

```html
<!DOCTYPE html>
<html lang="de">
<head>
<meta charset="utf-8">
<title>Morvelli Italia – Nero d'Avola Etikett</title>
<link rel="stylesheet" href="https://fonts.googleapis.com/css2?family=Barlow:wght@400;700&family=Kumbh+Sans:wght@800&display=swap">
<style>
  :root {
    --frame: #747474;
    --paper: #ffffff;
    --ink: #000000;
    --photo-light: #d9d9d9;
    --photo-dark: #6a6a6a;
  }
  * { margin: 0; padding: 0; box-sizing: border-box; }
  html, body {
    width: 1200px;
    height: 800px;
    overflow: hidden;
    background: var(--frame);
  }
  .label {
    position: absolute;
    left: 38px;
    top: 38px;
    width: 1124px;
    height: 724px;
    background: var(--paper);
    color: var(--ink);
  }
  .label__brand {
    position: absolute;
    left: 31px;
    top: 48px;
    font-family: "Barlow", sans-serif;
    font-weight: 700;
    font-size: 39px;
    letter-spacing: 4px;
    line-height: 1;
  }
  .label__variety {
    position: absolute;
    left: 28px;
    top: 183px;
    font-family: "Kumbh Sans", sans-serif;
    font-weight: 800;
    font-size: 108px;
    line-height: 113px;
    letter-spacing: 1px;
  }
  .label__region {
    position: absolute;
    left: 31px;
    top: 548px;
    font-family: "Barlow", sans-serif;
    font-weight: 700;
    font-size: 39px;
    letter-spacing: 4px;
    line-height: 1;
  }
  .label__vintage {
    position: absolute;
    left: 31px;
    top: 633px;
    font-family: "Barlow", sans-serif;
    font-weight: 400;
    font-size: 31px;
    letter-spacing: 2px;
    line-height: 1;
  }
  .label__artwork {
    position: absolute;
    left: 697px;
    top: 50px;
    width: 403px;
    height: 601px;
    background: linear-gradient(160deg, var(--photo-dark) 0%, var(--photo-light) 45%, var(--photo-light) 70%, var(--photo-dark) 100%);
  }
</style>
</head>
<body>
  <main class="label">
    <div class="label__brand">MORVELLI ITALIA</div>
    <h1 class="label__variety">NERO<br>D'AVOLA</h1>
    <div class="label__region">SIZILIEN</div>
    <div class="label__vintage">2022</div>
    <div class="label__artwork" role="img" aria-label="Schwarz-weiße Strichzeichnung eines langen Arkadengangs mit Bögen, Säulen und Schatten auf dem Steinboden"></div>
  </main>
</body>
</html>
```